New Company Business Card design

Looking for a corporate looking business card utilising my new logo design - the logo i would like embossed as one option and flat as another - simplistic but stylish - less is more - we are an import export business launching into the market - i would like a couple of options as main background - Grey or Black

```html
<!DOCTYPE html>
<html lang="en">
<head>
<meta charset="utf-8">
<title>Meridian Trade Partners — Business Card</title>
<link rel="stylesheet" href="https://fonts.googleapis.com/css2?family=Cinzel:wght@500&family=Inter:wght@400;500&display=swap">
<style>
  :root {
    --brand-blue: #1274c0;
    --brand-blue-deep: #0f62a8;
    --card-white: #ffffff;
    --accent-grey: #6d6e71;
    --text-grey: #4a4a4a;
    --stage: #2b2b2b;
  }
  * { margin: 0; padding: 0; box-sizing: border-box; }
  html, body { width: 1200px; height: 930px; overflow: hidden; }
  body {
    background: var(--stage);
    position: relative;
    font-family: "Inter", Arial, sans-serif;
  }
  .card {
    position: absolute;
    width: 620px;
    height: 356px;
    border-radius: 18px;
    overflow: hidden;
  }
  .card--front {
    left: 70px; top: 90px;
    background: var(--brand-blue);
  }
  .card--back {
    left: 510px; top: 480px;
    background: var(--card-white);
  }
  .wordmark {
    font-family: "Cinzel", Georgia, serif;
    font-weight: 500;
    letter-spacing: 0.04em;
    text-transform: uppercase;
    line-height: 1.15;
    position: absolute;
  }
  .card--front .wordmark {
    color: var(--card-white);
    font-size: 30px;
    left: 0; right: 0; top: 128px;
    text-align: center;
  }
  .card--front .tagline {
    position: absolute;
    left: 0; right: 0; top: 214px;
    text-align: center;
    color: var(--card-white);
    font-family: "Cinzel", Georgia, serif;
    font-size: 11px;
    letter-spacing: 0.28em;
    text-transform: uppercase;
  }
  .card--front .rule {
    position: absolute;
    left: 150px; right: 150px; top: 204px;
    height: 1px; background: var(--card-white);
  }
  .card--back .wordmark {
    color: var(--brand-blue);
    font-size: 19px;
    left: 34px; top: 44px;
  }
  .card--back .tagline {
    position: absolute;
    left: 34px; top: 100px;
    color: var(--accent-grey);
    font-family: "Cinzel", Georgia, serif;
    font-size: 8px;
    letter-spacing: 0.22em;
    text-transform: uppercase;
  }
  .holder {
    position: absolute;
    right: 34px; top: 40px;
    text-align: right;
  }
  .holder__name {
    color: var(--brand-blue);
    font-size: 24px;
    font-weight: 500;
    text-transform: uppercase;
    letter-spacing: 0.01em;
  }
  .holder__role {
    color: var(--text-grey);
    font-size: 14px;
    margin-top: 2px;
  }
  .divider {
    position: absolute;
    left: 34px; right: 34px; top: 140px;
    height: 1px; background: var(--brand-blue);
  }
  .address {
    position: absolute;
    right: 34px; top: 154px;
    text-align: right;
    color: var(--text-grey);
    font-size: 14px;
    line-height: 1.5;
  }
  .contact {
    position: absolute;
    left: 34px; top: 206px;
    list-style: none;
    color: var(--text-grey);
    font-size: 15px;
    line-height: 1.65;
  }
  .contact li { display: flex; align-items: center; gap: 10px; }
  .contact svg { width: 12px; height: 12px; fill: none; stroke: var(--brand-blue); stroke-width: 2; }
  .wave { position: absolute; left: 0; bottom: 0; width: 620px; height: 134px; }
</style>
</head>
<body>
  <section class="card card--front" aria-label="Card front">
    <div class="wordmark">Meridian Trade<br>Partners</div>
    <div class="rule"></div>
    <div class="tagline">Worldwide Supply, Local Service</div>
  </section>

  <section class="card card--back" aria-label="Card back">
    <div class="wordmark">Meridian Trade<br>Partners</div>
    <div class="tagline">Worldwide Supply, Local Service</div>

    <div class="holder">
      <div class="holder__name">Daniel Hart</div>
      <div class="holder__role">Director</div>
    </div>
    <div class="divider"></div>
    <div class="address">2210 Harbor View Rd<br>Fairview, CA 90417-3308</div>

    <ul class="contact">
      <li><svg viewBox="0 0 12 12"><path d="M2 1h3l1 3-2 1a7 7 0 0 0 3 3l1-2 3 1v3a1 1 0 0 1-1 1A10 10 0 0 1 1 2a1 1 0 0 1 1-1z"/></svg>555-204-7731</li>
      <li><svg viewBox="0 0 12 12"><rect x="1" y="2.5" width="10" height="7"/><path d="M1 3l5 4 5-4"/></svg>info@meridiantrade.com</li>
      <li><svg viewBox="0 0 12 12"><circle cx="6" cy="6" r="5"/><path d="M1 6h10M6 1c-2 3-2 7 0 10M6 1c2 3 2 7 0 10"/></svg>www.meridiantrade.com</li>
    </ul>

    <svg class="wave" viewBox="0 0 620 134" preserveAspectRatio="none" aria-hidden="true">
      <path d="M0 128 C180 124 300 104 380 62 C450 26 540 8 620 4 L620 134 L0 134 Z" fill="var(--accent-grey)"/>
      <path d="M0 132 C190 130 310 112 392 70 C460 36 545 20 620 15 L620 134 L0 134 Z" fill="var(--card-white)"/>
      <path d="M0 134 C200 134 320 120 400 80 C470 44 550 30 620 26 L620 134 Z" fill="var(--brand-blue)"/>
    </svg>
  </section>
</body>
</html>
```